BUSINESS CARD DESIGN

NAME- DALE VORSKIN
PHONE NUMER - 555- 714-9082
EMAIL- OFFICE@TRV-GROUNDMAKRZ.COM
BACK OF CARD- SPEACIALIZES IN LAND CLEARING, FORESTRY MUCLHING AND EXCAVATION

Contact Information for Business Card

NAME- DALE VORSKIN PHONE NUMER - 555- 714-9082 EMAIL- OFFICE@TRV-GROUNDMAKRZ.COM BACK OF CARD- SPEACIALIZES IN LAND CLEARING , MUCLHING AND EXCAVATION

```html
<!DOCTYPE html>
<html lang="en">
<head>
<meta charset="utf-8">
<title>TRV Groundmakrz – Business Card</title>
<link rel="stylesheet" href="https://fonts.googleapis.com/css2?family=Montserrat:wght@600;700&display=swap">
<style>
  :root {
    --gold: #f7b21c;
    --ink: #000000;
    --paper: #ffffff;
    --shadow: rgba(0, 0, 0, 0.55);
  }
  * { margin: 0; padding: 0; box-sizing: border-box; }
  html, body {
    width: 1200px; height: 1131px; overflow: hidden;
    background: var(--paper);
    font-family: "Montserrat", Arial, sans-serif;
  }
  .canvas { position: relative; width: 1200px; height: 1131px; }
  .card {
    position: absolute; left: 228px; width: 688px; height: 394px;
    box-shadow: 22px 22px 28px -6px var(--shadow);
    overflow: hidden;
  }
  .card--front { top: 151px; background: var(--paper); }
  .card--back { top: 626px; background: var(--ink); }

  .front-wave { position: absolute; left: 0; top: 0; width: 688px; height: 80px; }

  .brand { position: absolute; display: flex; flex-direction: column; align-items: center; color: var(--gold); }
  .brand__dot { border-radius: 50%; background: var(--gold); }
  .brand__name { font-weight: 700; text-align: center; line-height: 1.15; letter-spacing: 0.08em; }

  .card--front .brand { left: 36px; top: 118px; width: 240px; }
  .card--front .brand__dot { width: 72px; height: 72px; margin-bottom: 16px; }
  .card--front .brand__name { font-size: 19px; }

  .divider { position: absolute; left: 322px; top: 101px; width: 3px; height: 219px; background: var(--gold); }

  .person { position: absolute; left: 374px; top: 96px; color: var(--gold); }
  .person__name { font-size: 30px; font-weight: 600; letter-spacing: 0.01em; line-height: 1; }
  .person__role {
    display: inline-block; margin-top: 8px; font-size: 22px; font-weight: 600; line-height: 1;
    padding-bottom: 3px; border-bottom: 3px solid var(--gold);
  }

  .contacts { position: absolute; left: 384px; top: 216px; list-style: none; color: var(--gold); }
  .contacts__item { display: flex; align-items: center; height: 26px; margin-bottom: 14px; font-size: 15px; font-weight: 700; }
  .contacts__icon { width: 26px; height: 26px; margin-right: 15px; flex: none; }

  .card--back .brand { left: 0; right: 0; top: 78px; }
  .card--back .brand__dot { width: 120px; height: 120px; margin-bottom: 28px; }
  .card--back .brand__name { font-size: 28px; }

  .tagline {
    position: absolute; left: 0; right: 0; top: 344px; text-align: center;
    color: var(--gold); font-size: 13.5px; font-weight: 700; letter-spacing: 0.06em;
  }
</style>
</head>
<body>
<main class="canvas">
  <section class="card card--front">
    <svg class="front-wave" viewBox="0 0 688 80" preserveAspectRatio="none" aria-hidden="true">
      <path d="M0 0 H688 V53 C560 40 440 60 320 68 C220 75 90 60 0 0 Z" fill="var(--ink)"/>
    </svg>

    <div class="brand">
      <span class="brand__dot"></span>
      <span class="brand__name">TRV GROUNDMAKRZ<br>LLC</span>
    </div>

    <span class="divider"></span>

    <div class="person">
      <h1 class="person__name">DALE VORSKIN</h1>
      <span class="person__role">OWNER</span>
    </div>

    <ul class="contacts">
      <li class="contacts__item">
        <svg class="contacts__icon" viewBox="0 0 26 26" aria-hidden="true">
          <rect x="1" y="6" width="24" height="15" fill="var(--gold)"/>
          <path d="M1 6 L13 15 L25 6" fill="none" stroke="var(--paper)" stroke-width="2"/>
        </svg>
        @TRV-GROUNDMAKRZ.COM
      </li>
      <li class="contacts__item">
        <svg class="contacts__icon" viewBox="0 0 26 26" aria-hidden="true">
          <path d="M6 2 L10 7 L8 10 C9 13 12 17 16 18 L19 16 L24 20 L21 24 C12 23 3 14 2 5 Z" fill="none" stroke="var(--gold)" stroke-width="1.6" stroke-linejoin="round"/>
          <path d="M15 6 A6 6 0 0 1 20 11 M15 2 A10 10 0 0 1 24 11" fill="none" stroke="var(--gold)" stroke-width="1.6"/>
        </svg>
        +555- 714-9082
      </li>
      <li class="contacts__item">
        <svg class="contacts__icon" viewBox="0 0 26 26" aria-hidden="true">
          <g fill="none" stroke="var(--gold)" stroke-width="1.5">
            <circle cx="13" cy="13" r="11"/>
            <ellipse cx="13" cy="13" rx="5" ry="11"/>
            <path d="M2 13 H24 M4 7 H22 M4 19 H22 M13 2 V24"/>
          </g>
        </svg>
        www.trv-groundmakrz.com
      </li>
    </ul>
  </section>

  <section class="card card--back">
    <div class="brand">
      <span class="brand__dot"></span>
      <span class="brand__name">TRV GROUNDMAKRZ<br>LLC</span>
    </div>
    <p class="tagline">SPEACIALIZES IN LAND CLEARING , MUCLHING AND EXCAVATION</p>
  </section>
</main>
</body>
</html>
```